Kestrel Hearth Business Card Design

Design new, 2 sides, business cards for a residential and light commercial heating, air conditioning contractor.

Target Market(s)

Homeowners, small businesses

Industry/Entity Type

Business

Contact Information for Business Card

Dominic Westerhall
Phone - 862-415-2736
Email
Address - PO box 518
Brightwater NJ 07912
Website - www.KestrelHearthLLC.example

Requirements
Must have
• logo, company colors, standard size with no die cut, so I can use nova stamp

```html
<!DOCTYPE html>
<html lang="en">
<head>
<meta charset="utf-8">
<title>Kestrel Hearth Business Card</title>
<link href="https://fonts.googleapis.com/css2?family=Roboto:wght@400&family=Roboto+Condensed:wght@400;700&display=swap" rel="stylesheet">
<style>
  :root {
    --backdrop: #e9e9e9;
    --card-dark: #0b0b0d;
    --card-light: #f7f7f5;
    --maroon: #7f2434;
    --maroon-deep: #5a1a2a;
    --gold: #f3c56a;
    --accent-red: #d23a2c;
    --ink: #3a2a2e;
  }
  * { margin: 0; padding: 0; box-sizing: border-box; }
  html, body {
    width: 1200px; height: 576px; overflow: hidden;
    background: var(--backdrop);
  }
  .canvas { position: relative; width: 1200px; height: 576px; }

  .card {
    position: absolute; top: 138px;
    height: 294px;
    overflow: hidden;
  }
  .card--front { left: 81px; width: 485px; background: var(--card-dark); }
  .card--back { left: 602px; width: 482px; height: 290px; background: var(--card-light); }

  .brand-name {
    position: absolute;
    font-family: "Roboto Condensed", sans-serif;
    font-weight: 700;
    text-align: center;
    white-space: nowrap;
    transform: translate(-50%, -50%);
  }
  .card--front .brand-name {
    left: 242px; top: 131px;
    font-size: 40px; color: var(--gold);
  }
  .card--back .brand-name {
    left: 130px; top: 144px;
    font-size: 29px; color: var(--maroon);
  }

  .tagline-band {
    position: absolute; left: 0; top: 247px;
    width: 100%; height: 26px;
    background: var(--maroon);
    display: flex; align-items: center; justify-content: center;
    font-family: "Roboto", sans-serif;
    font-size: 12.5px; color: var(--gold);
  }
  .tagline-band .sep { margin: 0 5px; }

  .contact-block {
    position: absolute; left: 254px; top: 78px;
    font-family: "Roboto Condensed", sans-serif;
  }
  .person-name {
    font-size: 18px; font-weight: 700; color: var(--maroon-deep);
    line-height: 22px;
  }
  .person-title {
    font-size: 11.5px; color: var(--ink); margin-top: 1px;
  }
  .contact-list { list-style: none; margin-top: 18px; }
  .contact-list li {
    display: flex; align-items: center;
    font-size: 12px; color: var(--maroon-deep);
    height: 16.5px;
  }
  .contact-list svg {
    width: 11px; height: 11px; margin-right: 8px; flex: none;
    fill: var(--accent-red);
  }

  .base-strip {
    position: absolute; left: 0; bottom: 0;
    width: 100%; height: 6px; background: var(--maroon);
  }
</style>
</head>
<body>
<main class="canvas">
  <section class="card card--front" aria-label="Card front">
    <div class="brand-name">Kestrel Hearth</div>
    <div class="tagline-band">
      <span>Residential &amp; Light Commercial Heating</span>
      <span class="sep">•</span>
      <span>Air Conditioning Contractor</span>
    </div>
  </section>

  <section class="card card--back" aria-label="Card back">
    <div class="brand-name">Kestrel Hearth</div>
    <div class="contact-block">
      <p class="person-name">Dominic Westerhall</p>
      <p class="person-title">Managing Director</p>
      <ul class="contact-list">
        <li>
          <svg viewBox="0 0 24 24" aria-hidden="true"><path d="M3 8c0-3 4-5 9-5s9 2 9 5v2h-5V8H8v2H3V8zm2 4h14l2 9H3l2-9zm7 2a3 3 0 1 0 0 6 3 3 0 0 0 0-6z"/></svg>
          862-415-2736
        </li>
        <li>
          <svg viewBox="0 0 24 24" aria-hidden="true"><path d="M2 5h20v14H2V5zm2 2v.5l8 6 8-6V7H4z"/></svg>
          info@KestrelHearthLLC.example
        </li>
        <li>
          <svg viewBox="0 0 24 24" aria-hidden="true"><path d="M12 2a10 10 0 1 0 0 20 10 10 0 0 0 0-20zm0 2c1 0 2.3 2 2.8 5H9.2C9.7 6 11 4 12 4zM4.3 11h4.1c0 .7 0 1.4.1 2H4.3a8 8 0 0 1 0-2zm11.2 0h4.2a8 8 0 0 1 0 2h-4.2v-2zM9.2 15h5.6c-.5 3-1.8 5-2.8 5s-2.3-2-2.8-5zm1.3-4h3c.1.7.1 1.3 0 2h-3c-.1-.7-.1-1.3 0-2z"/></svg>
          www.KestrelHearthLLC.example
        </li>
        <li>
          <svg viewBox="0 0 24 24" aria-hidden="true"><path d="M12 1a8 8 0 0 0-8 8c0 6 8 14 8 14s8-8 8-14a8 8 0 0 0-8-8zm0 11a3 3 0 1 1 0-6 3 3 0 0 1 0 6z"/></svg>
          PO box 518 Brightwater NJ 07912
        </li>
      </ul>
    </div>
    <div class="base-strip"></div>
  </section>
</main>
</body>
</html>
```